Hearthline Insurance Provider Website

We are selling Hearthline Insurance policy / tenants Policy/Flood Insurance in USA in few states and planning expand nationally.

Our target audience are two folds: Customers (Buy policies) and Insurance Agents who wants to work with us to sell our policies to customers. But website should focus 80% on customers and 20% on agents. So, more customer focused user experience. Please note that there is no direct buy option for customers. They always go through insurance agents.

Customer focused, educational that makes buyer journey easy. We don’t want to come off as trying sell something as there is no direct sales involved from website.

Target Market(s)

Homeowners in USA and Insurance agent who sells these insurance.

Industry/Entity Type

Insurance

Number of Pages Required

4 page

Font styles to use
Other font styles liked:
• Open to suggestions

Colors

Designer to choose colors to be used in the design.

Requirements
Must have
• Three most important things: Trustworthy, Authentic, Simple
• Please use colors form logo and grays
• We like: www.hollowmere.com
• https://www.quillfenbrook.com/
• We need Agent Look up tool on home page similar to what is shown on example sites.
• Design:
• Home Page - Open to Ideas
• Insurance (Products) Landing Page - Info similar to: https://www.quillfenbrook.com/insurance/
• Agents Page - https://www.quillfenbrook.com/agents/
• Claims Page - Information similar to: https://www.quillfenbrook.com/claims-center/
• Site Navigation:
• Home
• Insurance
• Claims
• Agents
• About Us
• Contact Us
Nice to have
• Elegant, minimal and clean design that reflects trust and authenticity.
Should not have
• Slider or rotating images - prefer flat design. Not over powering design.

```html
<!DOCTYPE html>
<html lang="en">
<head>
<meta charset="utf-8">
<title>Insurance – Hearthline Insurance Co.</title>
<link rel="stylesheet" href="https://fonts.googleapis.com/css2?family=Source+Sans+3:wght@400;600;700&family=Questrial&display=swap">
<style>
:root{
  --navy:#1f3d8a;
  --navy-dark:#17306f;
  --red:#d5202f;
  --ink:#222;
  --text:#555;
  --soft:#f3f3f4;
  --footer:#353a44;
  --footer-text:#b9bcc2;
  --white:#fff;
}
*{margin:0;padding:0;box-sizing:border-box}
html,body{width:907px;height:1200px;overflow:hidden}
body{font-family:"Source Sans 3","Source Sans Pro",sans-serif;color:var(--text);background:var(--white);position:relative}
/* header */
.site-header{position:absolute;left:0;top:0;width:907px;height:57px;background:var(--white);z-index:2}
.brand{position:absolute;left:130px;top:11px;display:flex;align-items:center;gap:8px}
.brand-mark{width:28px;height:28px;background:var(--navy);border-radius:50%}
.brand-name{font-size:16px;font-weight:600;color:var(--navy);line-height:1.0;letter-spacing:.3px}
.brand-name small{display:block;font-size:10px;letter-spacing:2.2px;font-weight:400;margin-top:1px}
.main-nav{position:absolute;left:335px;top:21px;display:flex;gap:14px;font-size:10px;color:#444;font-weight:600}
.main-nav .active{color:var(--red)}
.btn{display:inline-flex;align-items:center;justify-content:center;color:var(--white);font-weight:600;border-radius:2px}
.btn-careers{position:absolute;left:642px;top:15px;width:67px;height:25px;background:var(--navy);font-size:10px}
.btn-login{position:absolute;left:711px;top:15px;width:66px;height:25px;background:var(--red);font-size:10px}
/* hero */
.hero{position:absolute;left:0;top:57px;width:907px;height:340px;
  background:
    radial-gradient(ellipse 150px 170px at 720px 120px,rgba(232,205,180,.85),rgba(232,205,180,0) 100%),
    radial-gradient(ellipse 200px 120px at 660px 290px,rgba(226,226,230,.9),rgba(226,226,230,0) 100%),
    radial-gradient(ellipse 130px 200px at 880px 90px,rgba(120,140,180,.7),rgba(120,140,180,0) 100%),
    radial-gradient(ellipse 260px 110px at 180px 300px,rgba(236,222,208,.9),rgba(236,222,208,0) 100%),
    linear-gradient(90deg,#f7f5f3 0%,#f1ebe5 40%,#e2d6ca 60%,#c9b8a6 78%,#9aa5bd 100%)}
.hero-text{position:absolute;left:130px;top:131px;width:292px}
.hero-text h1{font-family:"Questrial",sans-serif;font-weight:400;font-size:21px;color:var(--ink);margin-bottom:6px}
.hero-text p{font-size:10.6px;line-height:17px;color:#555;font-weight:600}
.products-band{position:absolute;left:0;top:397px;width:907px;height:216px;background:linear-gradient(180deg,#fff 0%,var(--soft) 100%)}
/* product cards */
.product{position:absolute;top:329px;width:150px;text-align:center}
.product-badge{margin:0 auto;width:136px;height:136px;border-radius:50%;background:var(--white);padding:6px}
.product-circle{width:124px;height:124px;border-radius:50%;background:linear-gradient(180deg,#2451a6 0%,var(--navy-dark) 100%);
  display:flex;flex-direction:column;align-items:center;justify-content:center;color:var(--white);font-size:10.5px;font-weight:600;line-height:12px}
.product-circle svg{margin-bottom:10px}
.product p{margin-top:10px;font-size:8.6px;line-height:14.7px;color:var(--text)}
.btn-more{margin-top:11px;width:66px;height:25px;background:var(--navy);font-size:9.5px;border:1px solid var(--navy-dark)}
/* states */
.states-title{position:absolute;left:0;top:640px;width:907px;text-align:center;font-family:"Questrial",sans-serif;font-weight:400;font-size:21px;color:var(--ink)}
.states-map{position:absolute;left:240px;top:680px;width:428px;height:272px;
  background:radial-gradient(ellipse 52% 48% at 52% 45%,#e6e6e6 0%,#ececec 60%,rgba(240,240,240,0) 100%)}
/* footer */
.site-footer{position:absolute;left:0;top:982px;width:907px;height:218px;background:var(--footer);color:var(--footer-text)}
.footer-brand{position:absolute;left:132px;top:28px;display:flex;align-items:center;gap:8px}
.footer-brand .brand-mark{background:var(--red)}
.footer-brand .brand-name{color:var(--white)}
.contact-phone{position:absolute;left:130px;top:67px;font-size:12.5px;color:#d8d9dc;font-weight:600}
.contact-mail{position:absolute;left:130px;top:84px;font-size:8.6px;color:#d8d9dc}
.social{position:absolute;left:130px;top:105px;display:flex;gap:4px}
.social span{width:23px;height:23px;border:1.4px solid #d0d2d6;border-radius:50%}
.footer-col{position:absolute;top:27px}
.footer-col h4{font-size:11px;color:var(--white);font-weight:600;margin-bottom:8px}
.footer-col a{display:block;font-size:8.8px;line-height:14.6px;color:var(--footer-text);text-decoration:none}
.btn-agent{position:absolute;left:407px;top:91px;width:106px;height:30px;background:var(--red);font-size:11px;gap:5px}
.copyright{position:absolute;left:0;top:158px;width:907px;text-align:center;font-size:8.6px;line-height:14.6px;color:var(--footer-text)}
</style>
</head>
<body>
<header class="site-header">
  <div class="brand"><span class="brand-mark"></span><span class="brand-name">HEARTHLINE<small>INSURANCE CO.</small></span></div>
  <nav class="main-nav"><span>Home</span><span class="active">Insurance</span><span>About Us</span><span>Claims</span><span>Agents</span><span>Contact Us</span></nav>
  <span class="btn btn-careers">
    <svg width="9" height="9" viewBox="0 0 10 10"><circle cx="5" cy="3" r="2.3" fill="#fff"/><path d="M1 10c0-3 2-4.5 4-4.5S9 7 9 10z" fill="#fff"/></svg>&nbsp;Careers</span>
  <span class="btn btn-login">
    <svg width="8" height="9" viewBox="0 0 8 10"><rect x="0.5" y="4.5" width="7" height="5" fill="#fff"/><path d="M2 4.5V3a2 2 0 0 1 4 0v1.5" stroke="#fff" fill="none" stroke-width="1.3"/></svg>&nbsp;Login</span>
</header>

<section class="hero" role="img" aria-label="Photo of a smiling couple relaxing on a sofa with a laptop in a bright living room"></section>
<div class="hero-text">
  <h1>Insurance</h1>
  <p>No matter where you live, protecting your belongings is important. That's why Hearthline offers a variety of Property &amp; Casualty insurance policies, all tailored to fit your individual needs.</p>
</div>

<div class="products-band"></div>

<div class="product" style="left:130px">
  <div class="product-badge"><div class="product-circle">
    <svg width="36" height="32" viewBox="0 0 36 32"><path d="M18 2L2 16h4v14h9v-9h6v9h9V16h4z" fill="#fff"/></svg>Homeowners</div></div>
  <p>Nullam ac urna eu felis dapibus neque condimentum sit amet a augue. Sed non neque elit. Sed ut imperdiet nisi. ut aliquam massa nisl quis neque. Suspendisse in orci enim.</p>
  <span class="btn btn-more">Read More</span>
</div>
<div class="product" style="left:296px">
  <div class="product-badge"><div class="product-circle">
    <svg width="34" height="36" viewBox="0 0 34 36"><rect x="4" y="2" width="26" height="34" fill="#fff"/><g fill="#1f3d8a"><rect x="8" y="6" width="4" height="4"/><rect x="15" y="6" width="4" height="4"/><rect x="22" y="6" width="4" height="4"/><rect x="8" y="13" width="4" height="4"/><rect x="15" y="13" width="4" height="4"/><rect x="22" y="13" width="4" height="4"/><rect x="8" y="20" width="4" height="4"/><rect x="15" y="20" width="4" height="4"/><rect x="22" y="20" width="4" height="4"/><rect x="14" y="28" width="6" height="8"/></g></svg>Renters/Condo</div></div>
  <p>Nullam ac urna eu felis dapibus neque condimentum sit amet a augue. Sed non neque elit. Sed ut imperdiet nisi. ut aliquam massa nisl quis neque. Suspendisse in orci enim.</p>
  <span class="btn btn-more">Read More</span>
</div>
<div class="product" style="left:462px">
  <div class="product-badge"><div class="product-circle">
    <svg width="48" height="34" viewBox="0 0 48 34"><path d="M16 2L1 15h4v17h22V15h4z" fill="#fff"/><g fill="#1f3d8a"><rect x="10" y="18" width="5" height="5"/><rect x="17" y="18" width="5" height="5"/><rect x="10" y="25" width="5" height="5"/><rect x="17" y="25" width="5" height="5"/></g><path d="M38 4c2 6 8 9 8 18a8 8 0 0 1-16 0c0-5 3-6 3-10 2 2 3 4 3 6 2-4 3-8 2-14z" fill="#fff"/></svg>Dwelling Fire</div></div>
  <p>Nullam ac urna eu felis dapibus neque condimentum sit amet a augue. Sed non neque elit. Sed ut imperdiet nisi. ut aliquam massa nisl quis neque. Suspendisse in orci enim.</p>
  <span class="btn btn-more">Read More</span>
</div>
<div class="product" style="left:628px">
  <div class="product-badge"><div class="product-circle">
    <svg width="38" height="38" viewBox="0 0 38 38"><path d="M19 2a10 10 0 0 0-10 10c0 8 10 18 10 18s10-10 10-18A10 10 0 0 0 19 2z" fill="#fff"/><circle cx="19" cy="12" r="4" fill="#1f3d8a"/><path d="M8 28l-5 9h32l-5-9" stroke="#fff" stroke-width="2" fill="none"/></svg>Agent Locator<br>Tool</div></div>
  <p>Nullam ac urna eu felis dapibus neque condimentum sit amet a augue. Sed non neque elit. Sed ut imperdiet nisi. ut aliquam massa nisl quis neque. Suspendisse in orci enim.</p>
  <span class="btn btn-more">Read More</span>
</div>

<h2 class="states-title">Our Serving States</h2>
<div class="states-map" role="img" aria-label="Map of the United States in light gray with red pins marking the states served"></div>

<footer class="site-footer">
  <div class="footer-brand"><span class="brand-mark"></span><span class="brand-name">HEARTHLINE<small>INSURANCE CO.</small></span></div>
  <div class="contact-phone">1800 555 0142</div>
  <div class="contact-mail">info@hearthlineinsurance.co</div>
  <div class="social" aria-label="Social links"><span></span><span></span><span></span><span></span></div>
  <div class="footer-col" style="left:296px"><h4>Our Company</h4><a>Home</a><a>Insurance</a><a>About Us</a><a>Claims</a><a>Agents</a></div>
  <div class="footer-col" style="left:406px"><h4>Login to Your Account</h4><a>Agents Login</a><a>Clients login</a></div>
  <span class="btn btn-agent">
    <svg width="12" height="12" viewBox="0 0 12 12"><circle cx="5" cy="5" r="3.8" stroke="#fff" stroke-width="1.4" fill="none"/><path d="M8 8l3.3 3.3" stroke="#fff" stroke-width="1.5"/></svg>Find an Agent</span>
  <div class="footer-col" style="left:555px"><h4>Customer Support</h4><a>FAQs</a><a>Resources</a><a>Report a Claim</a><a>Find an Agent</a></div>
  <div class="footer-col" style="left:683px"><h4>Connect With Us</h4><a>Support</a><a>Careers</a></div>
  <div class="copyright">Copyright ©2018 Hearthline Insurance. All Rights Reserved<br>Terms of Use &nbsp;-&nbsp; Privacy Policy &nbsp;-&nbsp; Sitemap</div>
</footer>
</body>
</html>
```